VelkaVision.com

Complete Website Design (Godaddy) and company Branding / Logo Design. The products will sell are only done in-person and are installed. So this site does not need to be an e-commerce site. We will only be giving out information and collecting customer inquires. Website will only need to be about 3 to 5 pages.

```html
<!DOCTYPE html>
<html lang="en">
<head>
<meta charset="utf-8">
<title>Velka Vision — TV Installation</title>
<link rel="stylesheet" href="https://fonts.googleapis.com/css2?family=Open+Sans:wght@400;600;700;800&family=Ubuntu:wght@700&family=Roboto:wght@400;500;700&display=swap">
<style>
  :root {
    --blue: #1fa3dc;
    --blue-deep: #1b8fca;
    --orange: #f4761c;
    --ink: #0b0b0b;
    --grey: #5e5e5e;
    --hero-bg: #eef0f2;
    --soft: #f7f7f8;
    --white: #ffffff;
    --footer: #050505;
  }
  * { box-sizing: border-box; margin: 0; padding: 0; }
  html, body { width: 677px; height: 1200px; overflow: hidden; background: var(--white); }
  body { position: relative; font-family: "Open Sans", Arial, sans-serif; }
  .abs { position: absolute; }

  .top-rule { left: 0; top: 0; width: 677px; height: 2px; background: var(--orange); }

  .brand { left: 63px; top: 42px; font-family: "Ubuntu", "Open Sans", sans-serif; font-weight: 700; font-size: 17px; color: var(--blue); display: flex; align-items: center; gap: 5px; }
  .brand-mark { width: 10px; height: 10px; border: 2px solid var(--blue); border-radius: 50%; }

  .info-icon { width: 29px; height: 29px; border-radius: 50%; border: 1.5px solid var(--orange); display: flex; align-items: center; justify-content: center; }
  .info-icon span { width: 21px; height: 21px; border-radius: 50%; background: var(--blue); display: flex; align-items: center; justify-content: center; }
  .info-label { font-size: 6.3px; font-weight: 700; color: var(--orange); letter-spacing: .2px; }
  .info-value { font-size: 11px; font-weight: 600; color: var(--blue); margin-top: 3px; }

  .reviews { left: 559px; top: 8px; font-size: 6.6px; color: var(--grey); line-height: 1.55; }
  .reviews .stars { color: var(--orange); font-size: 7.5px; letter-spacing: .5px; }
  .reviews .source { color: var(--blue); font-weight: 600; }

  .nav { left: 0; top: 48px; width: 677px; height: 27px; }
  .nav-links { left: 212px; top: 48px; height: 27px; display: flex; align-items: center; font-size: 7.6px; font-weight: 700; color: var(--white); }
  .nav-links a { color: inherit; text-decoration: none; }
  .social { display: flex; gap: 5px; }
  .social i { display: block; border: 1px solid var(--white); border-radius: 50%; }
  .nav-social { left: 531px; top: 53px; }
  .nav-social i { width: 16px; height: 16px; }

  .hero-art { left: 0; top: 74px; width: 677px; height: 302px; }
  .welcome { left: 63px; top: 134px; font-size: 20px; font-weight: 800; color: var(--orange); letter-spacing: .5px; }
  .hero-title { left: 61px; top: 160px; font-size: 35px; font-weight: 800; color: var(--ink); letter-spacing: .3px; }
  .hero-copy { left: 63px; top: 214px; width: 265px; font-size: 10.3px; line-height: 18.5px; color: var(--grey); }
  .btn { display: flex; align-items: center; justify-content: center; border-radius: 3px; font-weight: 700; color: var(--white); font-size: 8.6px; }
  .btn-blue { background: var(--blue); }
  .btn-orange { background: var(--orange); }

  .about-bg { left: 0; top: 376px; width: 677px; height: 410px; background: linear-gradient(180deg, var(--white), var(--soft) 40%, var(--soft)); }
  .about-frame { left: 75px; top: 437px; width: 277px; height: 265px; border: 1px solid var(--blue); }
  .about-photo { left: 63px; top: 451px; width: 275px; height: 264px; background: linear-gradient(110deg, #16394f 0%, #2b8fa8 45%, #58c4da 70%, #1d5065 100%); box-shadow: 0 4px 14px rgba(0,0,0,.12); }
  .about-title { left: 390px; top: 463px; font-size: 24px; font-weight: 800; color: var(--ink); }
  .about-copy { left: 390px; width: 230px; font-size: 7.9px; line-height: 16px; color: var(--grey); }

  .quote-art { left: 0; top: 760px; width: 677px; height: 398px; }
  .quote-title { left: 0; top: 842px; width: 677px; text-align: center; font-size: 24px; font-weight: 800; color: var(--white); letter-spacing: .3px; }
  .quote-sub { left: 0; top: 884px; width: 677px; text-align: center; font-size: 10px; color: var(--white); }
  .field { background: var(--white); border-radius: 6px; font-family: "Roboto", sans-serif; font-size: 8.4px; color: #4a4a4a; padding: 0 16px; display: flex; align-items: center; }
  .field-area { align-items: flex-start; padding-top: 15px; }
  .submit { background: var(--orange); border-radius: 6px; font-family: "Roboto", sans-serif; font-weight: 700; font-size: 9px; color: var(--white); display: flex; align-items: center; justify-content: center; }

  .footer { left: 0; top: 1157px; width: 677px; height: 43px; background: var(--footer); }
  .copyright { left: 63px; top: 1166px; font-size: 10.8px; color: var(--white); }
  .footer-social { left: 510px; top: 1168px; gap: 7px; }
  .footer-social i { width: 21px; height: 21px; }
</style>
</head>
<body>
  <div class="abs top-rule"></div>

  <header>
    <div class="abs brand"><span class="brand-mark"></span>Velka Vision</div>

    <div class="abs" style="left:280px;top:10px;display:flex;gap:10px;align-items:center;">
      <div class="info-icon"><span>
        <svg width="10" height="10" viewBox="0 0 24 24"><path fill="#fff" d="M6.6 10.8a15 15 0 0 0 6.6 6.6l2.2-2.2c.3-.3.7-.4 1-.2 1.1.4 2.3.6 3.6.6.6 0 1 .4 1 1V20c0 .6-.4 1-1 1A17 17 0 0 1 3 4c0-.6.4-1 1-1h3.5c.6 0 1 .4 1 1 0 1.3.2 2.5.6 3.6.1.3 0 .7-.2 1z"/></svg>
      </span></div>
      <div><div class="info-label">CALL US:</div><div class="info-value">+1 555 014 2290</div></div>
    </div>

    <div class="abs" style="left:427px;top:10px;display:flex;gap:10px;align-items:center;">
      <div class="info-icon"><span>
        <svg width="10" height="10" viewBox="0 0 24 24"><circle cx="12" cy="12" r="8" fill="none" stroke="#fff" stroke-width="2.6"/><path d="M12 8v4.5h3" fill="none" stroke="#fff" stroke-width="2.2"/></svg>
      </span></div>
      <div><div class="info-label">WORKING HOURS:</div><div class="info-value">9 AM - 6 PM</div></div>
    </div>

    <div class="abs reviews">
      <div class="stars">★★★★☆</div>
      <div>450<sup style="font-size:4px">+</sup> 5 Start Reviews</div>
      <div class="source">Reviewly</div>
    </div>

    <svg class="abs nav" viewBox="0 0 677 27" aria-hidden="true">
      <polygon points="199,0 514,0 503,27 186,27" fill="var(--blue)"/>
      <polygon points="514,0 622,0 634,27 503,27" fill="var(--orange)"/>
    </svg>
    <nav class="abs nav-links">
      <a style="width:54px">Home</a>
      <a style="width:66px">About Us</a>
      <a style="width:63px">Services</a>
      <a style="width:48px">Blog</a>
      <a>Contact Us</a>
    </nav>
    <div class="abs social nav-social"><i></i><i></i><i></i><i></i></div>
  </header>

  <section>
    <svg class="abs hero-art" viewBox="0 74 677 302" aria-hidden="true">
      <rect x="0" y="74" width="677" height="302" fill="var(--hero-bg)"/>
      <polygon points="0,370 349,354 677,375 677,376 0,376" fill="var(--white)"/>
      <polygon points="0,330 349,353 0,371" fill="var(--orange)"/>
    </svg>
    <div class="abs" role="img" aria-label="Technician kneeling beside a wall-mounted TV, testing cables on a media console"
         style="left:316px;top:74px;width:361px;height:301px;background:linear-gradient(100deg,rgba(238,240,242,0) 0%,#cfd1d5 30%,#9fa3aa 60%,#e4e0da 100%);clip-path:polygon(0 0,100% 0,100% 100%,8% 93%,0 93%);"></div>

    <div class="abs welcome">WELCOME TO</div>
    <h1 class="abs hero-title">VELKA VISION</h1>
    <p class="abs hero-copy">I must explain to you how all this mistaken idea of denouncing pleasure and praising pain was born</p>
    <div class="abs btn btn-blue" style="left:63px;top:265px;width:75px;height:24px;">Get Started</div>
    <div class="abs btn btn-orange" style="left:148px;top:265px;width:75px;height:24px;">Free Quote</div>
  </section>

  <section>
    <div class="abs about-bg"></div>
    <div class="abs about-photo" role="img" aria-label="Installer mounting a ceiling projector"></div>
    <div class="abs about-frame"></div>
    <h2 class="abs about-title">ABOUT US</h2>
    <p class="abs about-copy" style="top:502px;">At vero eos et accusamus et iusto odio dignissimos ducimus qui blanditiis praesentium voluptatum deleniti atque corrupti quos dolores et quas molestias excepturi sint occaecati cupiditate non provident</p>
    <p class="abs about-copy" style="top:582px;">Similique sunt in culpa qui officia deserunt mollitia animi, id est laborum et dolorum fuga. Et harum quidem rerum facilis est et expedita distinctio. Nam libero tempore, cum soluta nobis est eligendi optio cumque</p>
    <div class="abs btn btn-orange" style="left:390px;top:662px;width:67px;height:21px;font-size:7.8px;">Read More</div>
  </section>

  <section>
    <svg class="abs quote-art" viewBox="0 760 677 398" role="img" aria-label="Living room with a home theater setup, tinted blue">
      <defs>
        <linearGradient id="quoteBg" x1="0" y1="0" x2="1" y2="1">
          <stop offset="0" stop-color="#1e9ad6"/>
          <stop offset=".6" stop-color="#1b93cf"/>
          <stop offset="1" stop-color="#1886c0"/>
        </linearGradient>
      </defs>
      <polygon points="0,779 677,816 677,1158 0,1158" fill="url(#quoteBg)"/>
      <polygon points="335,798 677,763 677,818" fill="var(--orange)"/>
    </svg>
    <h2 class="abs quote-title">REQUEST A QUOTE</h2>
    <p class="abs quote-sub">Sed ut perspiciatis unde omnis iste natus error sit voluptatem accusantium doloremqu</p>

    <div class="abs field" style="left:100px;top:921px;width:232px;height:38px;">Full Name</div>
    <div class="abs field" style="left:100px;top:969px;width:232px;height:38px;">Email Address</div>
    <div class="abs field" style="left:100px;top:1017px;width:232px;height:38px;">Contact Number</div>
    <div class="abs submit" style="left:100px;top:1065px;width:232px;height:38px;">SUBMIT NOW</div>
    <div class="abs field field-area" style="left:345px;top:921px;width:232px;height:182px;">Message</div>
  </section>

  <footer>
    <div class="abs footer"></div>
    <div class="abs copyright">(C) Copyright 2024 | All Rights Reserved</div>
    <div class="abs social footer-social"><i></i><i></i><i></i><i></i></div>
  </footer>
</body>
</html>
```